Pages That Pay Dividends - book cover (front panel only)

I want a book cover (for print and ebook) in a distinctive, quirky style that can be repurposed for podcast artwork too. Full brief supplied.
The book is a practical, accessible handbook for anyone thinking about writing a book to build their business, with a wide range of tips and techniques to help plan, write, publishing and promote a book that’s integrated with your platform and works to build your reputation, network and credibility from day 1.
The target audience is experts in business, particularly owners of SMEs with an established online and offline platform (eg speaking, training, consulting) who want to add a book to take their business to the next level.
I want the design to be strong and distinctive, slightly quirky without being gimmicky, with the focus on typography.

Target Market(s)

Those writing a book based on their expertise to build their business

Industry/Entity Type

Publishing Company

Font styles to use
Serif
Sans Serif
Decorative

Colors

Designer to choose colors to be used in the design.

Requirements
Must have
• Commercially appealing book cover design, with application files and copyright supplied, front panel only, 5.5 x 8.5 inch format. Must work at both full size and thumbnail.
Nice to have
• A distinctive style that could be applied across other products in my portfolio.

```html
<!DOCTYPE html>
<html lang="en">
<head>
<meta charset="utf-8">
<title>Pages That Pay Dividends – Front Cover</title>
<link rel="stylesheet" href="https://fonts.googleapis.com/css2?family=Kaushan+Script&family=Amatic+SC:wght@700&display=swap">
<style>
  :root {
    --backdrop: #f1f1f1;
    --board: #121212;
    --chalk: #ffffff;
    --lime: #9bb52f;
    --lime-deep: #2c3311;
    --orange-deep: #3a2412;
    --purple-deep: #2a1530;
  }
  * { margin: 0; padding: 0; box-sizing: border-box; }
  html, body {
    width: 1200px; height: 1200px; overflow: hidden;
    background: var(--backdrop);
  }
  .cover {
    position: absolute; left: 244px; top: 50px;
    width: 712px; height: 1100px;
    background: var(--board);
    overflow: hidden;
  }
  .bulb-illustration {
    position: absolute; left: 24px; top: 0;
    width: 664px; height: 400px;
    background: linear-gradient(100deg,
      var(--purple-deep) 0%,
      var(--orange-deep) 28%,
      var(--lime-deep) 50%,
      var(--orange-deep) 72%,
      var(--purple-deep) 100%);
  }
  h1 { font-weight: normal; }
  .title {
    position: absolute; left: 0; width: 100%;
    text-align: center;
    font-family: "Kaushan Script", cursive;
    line-height: 1;
    white-space: nowrap;
  }
  .title-line-1 { top: 430px; font-size: 118px; color: var(--chalk); }
  .title-line-2 { top: 565px; font-size: 118px; color: var(--chalk); }
  .title-line-3 { top: 690px; font-size: 122px; color: var(--lime); }
  .subtitle {
    position: absolute; left: 0; top: 862px; width: 100%;
    text-align: center;
    font-family: "Amatic SC", sans-serif;
    font-weight: 700;
    text-transform: uppercase;
    font-size: 34px; letter-spacing: 4px; line-height: 1.15;
    color: var(--chalk);
  }
  .author {
    position: absolute; left: 0; top: 962px; width: 100%;
    text-align: center;
    font-family: "Kaushan Script", cursive;
    font-size: 72px; line-height: 1;
    color: var(--lime);
  }
</style>
</head>
<body>
  <main class="cover">
    <div class="bulb-illustration" role="img" aria-label="Illustration: hanging outline light bulbs labelled Vision, Innovation, Goals, Growth, Success, Research, Teamwork and Strategy, with the central Success bulb glowing and a thin ladder leading down from it"></div>
    <h1>
      <span class="title title-line-1">Pages That</span>
      <span class="title title-line-2">Pay</span>
      <span class="title title-line-3">Dividends</span>
    </h1>
    <p class="subtitle">Clever ways to plan and write a book<br>that works harder for your business</p>
    <p class="author">Miriam Hale</p>
  </main>
</body>
</html>
```